Greeting Card Design - Bright Hearts Open Pages

Hi there

Thank you for taking the time to read about this project.

The project is for a range of greeting cards for the gay and lesbian community. The brand is called "Bright Hearts Open Pages".

In this project I require four designs in total (designs for homosexual couples, two for men and two for women). The designs need to reflect the general concept of being in love.

I am looking for variety (fun and funky, as well as modern and classy - please design to your tastes and I will give feedback).

I will work with each designer closely and provide the words for the cards as the designs are developed.

Thank you for considering this project.
Updates

I'm currently having issues with the craft huddle website and it won't let me upload files to show the logo. I will do so as soon as the website allows me. Thanks

Target Market(s)

Gay and lesbian community.

Industry/Entity Type

Community

Requirements
Must have
• I am looking for variety in the range. I would like designs that are modern and classy range; and also designs that are fun and funky.
Nice to have
• Hand drawings are good for the fun range, so is colour.
The classy range can be symbolic (e.g. holding hands) or black and whites.
Should not have
• Please do not use rainbows or rainbow coloured font.

```html
<!DOCTYPE html>
<html lang="en">
<head>
<meta charset="utf-8">
<title>Bright Hearts Open Pages – My love card</title>
<link rel="stylesheet" href="https://fonts.googleapis.com/css2?family=Nothing+You+Could+Do&family=Open+Sans:wght@600&display=swap">
<style>
  :root {
    --card-red: #be1e2d;
    --paper: #ffffff;
    --ink: #3a3a3a;
    --trim: #333333;
    --string: #555555;
    --photo-light: #b3b3b3;
    --photo-mid: #8a8a8a;
    --photo-dark: #5e5e5e;
  }
  * { margin: 0; padding: 0; box-sizing: border-box; }
  html, body {
    width: 1200px;
    height: 793px;
    overflow: hidden;
    background: var(--paper);
  }
  .sheet {
    position: relative;
    width: 1200px;
    height: 793px;
  }

  /* Outside spread: front cover */
  .card-front {
    position: absolute;
    left: 16px;
    top: 16px;
    width: 556px;
    height: 765px;
    border: 1px solid var(--trim);
    background: var(--paper);
    overflow: hidden;
  }
  .cover-photo {
    position: absolute;
    left: 0;
    top: 381px;
    width: 100%;
    height: 384px;
    background:
      linear-gradient(90deg, var(--photo-mid) 0%, var(--photo-dark) 36%, var(--photo-light) 48%, var(--photo-light) 68%, var(--photo-mid) 78%, var(--photo-mid) 100%);
  }
  .title-tag {
    position: absolute;
    left: 0;
    top: 432px;
    width: 244px;
    height: 72px;
    background: var(--card-red);
  }
  .title-tag h1 {
    position: absolute;
    left: 42px;
    top: 6px;
    font-family: "Nothing You Could Do", cursive;
    font-weight: 400;
    font-size: 42px;
    line-height: 1.2;
    color: var(--paper);
    white-space: nowrap;
  }
  .balloon {
    position: absolute;
    left: 375px;
    top: 199px;
    width: 134px;
    height: 182px;
  }
  .balloon svg { position: absolute; left: 0; top: 0; }
  .balloon-name {
    position: absolute;
    left: 17px;
    top: 44px;
    width: 100px;
    text-align: center;
    font-family: "Open Sans", sans-serif;
    font-weight: 600;
    font-size: 13px;
    line-height: 1.3;
    color: var(--paper);
  }

  /* Inside spread: message page */
  .card-inside {
    position: absolute;
    left: 632px;
    top: 16px;
    width: 556px;
    height: 765px;
    border: 16px solid var(--card-red);
    background: var(--paper);
  }
  .fold-line {
    position: absolute;
    left: -16px;
    right: -16px;
    top: 365px;
    border-top: 1px dashed var(--trim);
  }
  .message {
    position: absolute;
    left: 0;
    right: 0;
    top: 524px;
    text-align: center;
    font-family: "Nothing You Could Do", cursive;
    font-size: 16px;
    color: var(--ink);
    white-space: nowrap;
  }
</style>
</head>
<body>
  <main class="sheet">
    <section class="card-front">
      <div class="cover-photo" role="img" aria-label="Black and white photograph of two people in jeans holding hands"></div>
      <div class="title-tag"><h1>My love...</h1></div>
      <div class="balloon">
        <svg width="134" height="182" viewBox="0 0 134 182" aria-hidden="true">
          <path d="M68 134 C63 150, 70 164, 62 182" fill="none" stroke="var(--string)" stroke-width="1.2"/>
          <path d="M70 134 C72 152, 65 166, 64 182" fill="none" stroke="var(--string)" stroke-width="1.2"/>
          <circle cx="67" cy="67" r="67" fill="var(--card-red)"/>
        </svg>
        <div class="balloon-name">Bright Hearts Open Pages</div>
      </div>
    </section>

    <section class="card-inside">
      <div class="fold-line"></div>
      <p class="message">You are my favourite person in the world</p>
    </section>
  </main>
</body>
</html>
```